Professional & attention grabbing.

A business card design, front and back. I already have a logo I will attach, but I am open to something new as well.
Things to include:
Name:
Title:
Phone:
Email:
Wanting something that is professional but attention grabbing.
Also we do a lot of work using drones on natural gas pipelines (leading the future)if you want to include any of that. I'm open to ideas.
Target Market(s)
Natural gas transmission industry / greenhouse gas mitigation industry
Industry/Entity Type
Business
Colors
Designer to choose colors to be used in the design.
Look and feel
Each slider illustrates characteristics of the customer's brand and the style your logo design should communicate.

```html
<!DOCTYPE html>
<html lang="en">
<head>
<meta charset="utf-8">
<title>KT Field Inspections – Business Card</title>
<link rel="stylesheet" href="https://fonts.googleapis.com/css2?family=Source+Sans+3:wght@400;600&display=swap">
<style>
  :root {
    --page-bg: #e9e7e5;
    --card-light: #f7f7f7;
    --card-dark: #3a3a3c;
    --accent-red: #c8161d;
    --ink: #2f2f31;
    --ink-soft: #3c3c3e;
    --white: #ffffff;
  }
  * { margin: 0; padding: 0; box-sizing: border-box; }
  html, body {
    width: 1200px; height: 900px; overflow: hidden;
    background: var(--page-bg);
    font-family: "Source Sans 3", Arial, sans-serif;
  }
  .business-card {
    position: absolute; left: 274px; top: 248px;
    width: 652px; height: 403px;
    background: var(--card-light);
    box-shadow: 0 10px 30px rgba(0,0,0,0.15);
    overflow: hidden;
  }
  .accent-stripe {
    position: absolute; left: 344px; top: 0;
    width: 9px; height: 100%;
    background: var(--accent-red);
  }
  .dark-panel {
    position: absolute; left: 353px; top: 0; right: 0; bottom: 0;
    background: var(--card-dark);
  }
  .brand {
    position: absolute; left: 35px; top: 78px;
    display: flex; align-items: center; gap: 12px;
  }
  .brand-square {
    width: 30px; height: 30px; background: var(--accent-red);
  }
  .brand-name {
    font-weight: 600; font-size: 26px; color: var(--ink);
    letter-spacing: 0.2px; line-height: 1;
  }
  .person { position: absolute; left: 35px; top: 248px; }
  .person-name {
    font-weight: 600; font-size: 22px; color: var(--accent-red);
    text-transform: uppercase; letter-spacing: 0.3px; line-height: 1.1;
  }
  .person-title {
    font-size: 17px; color: var(--ink-soft); line-height: 1.3;
  }
  .contact-list {
    position: absolute; left: 37px; top: 324px;
    list-style: none;
  }
  .contact-item {
    display: flex; align-items: center; gap: 8px;
    font-size: 17px; color: var(--ink); line-height: 24px;
  }
  .contact-icon { width: 14px; height: 14px; fill: var(--accent-red); }
  .address {
    position: absolute; right: 35px; top: 154px;
    text-align: right; color: var(--white);
    font-size: 17px; line-height: 24px; font-style: normal;
  }
</style>
</head>
<body>
  <section class="business-card">
    <div class="accent-stripe"></div>
    <div class="dark-panel"></div>

    <div class="brand">
      <span class="brand-square"></span>
      <span class="brand-name">KT Field Inspections</span>
    </div>

    <div class="person">
      <p class="person-name">Daniel Reyes</p>
      <p class="person-title">Managing Director</p>
    </div>

    <ul class="contact-list">
      <li class="contact-item">
        <svg class="contact-icon" viewBox="0 0 24 24" aria-hidden="true"><path d="M6.6 10.8a15.1 15.1 0 0 0 6.6 6.6l2.2-2.2a1 1 0 0 1 1-.25 11.4 11.4 0 0 0 3.6.57 1 1 0 0 1 1 1V20a1 1 0 0 1-1 1A17 17 0 0 1 3 4a1 1 0 0 1 1-1h3.5a1 1 0 0 1 1 1c0 1.25.2 2.45.57 3.6a1 1 0 0 1-.25 1z"/></svg>
        (055)987654321
      </li>
      <li class="contact-item">
        <svg class="contact-icon" viewBox="0 0 24 24" aria-hidden="true"><path d="M2 5h20v14H2z M2 5l10 7 10-7" stroke="#f7f7f7" stroke-width="1.6"/></svg>
        hello@ktfield.com
      </li>
    </ul>

    <address class="address">
      4820, Harbor Line Road<br>
      Northland County, 204518.
    </address>
  </section>
</body>
</html>
```